Business Card for Polygraph business in Africa

Business Card . Polygraph Examiner based in Tanzania, East Africa.
Business Card will be used to disseminate contact information to potential clients.
It should convey that I am a professional specifically in the polygraph field and perform my work with integrity.

I have attached the business card that I'm currently using, which I threw together myself initially. It's not professional enough.

Target Market(s)

Banks, Accounting Firms, Government Ministries, Gas, Oil, & Gemstone Mining Concerns, Wildlife Conservation NGOs, International companies located in East Africa.

Industry/Entity Type

Business

Contact Information for Business Card

Veritrace Kilonga
Miriam Holloway
PO Box 48317
Arusha, Tanzania
+255 612 839 274
miriamholloway@postvale.example

Colors
00a990
f37122
faa54b

Requirements
Must have
• - Veritrace Kilonga (with the word "Polygraph" being more prominent than the word "Tanzania")
• - Forensic Examinations
• - Employment Screening
• - Should contain a logo of the Continental Truthline Society (of which I'm a member)
• - I would like an accent design (such as the polygraph "squiggles" of a cardio tracing or such as that)
• - My contact information (less prominent, but large enough to read legibly). I would also consider putting the contact information on the second side of the card.
Nice to have
• My color suggestions are changeable.
Should not have
• Anything "cutesy" or "cartoonish"

```html
<!DOCTYPE html>
<html lang="en">
<head>
<meta charset="utf-8">
<title>Veritrace Kilonga – Business Card</title>
<link rel="stylesheet" href="https://fonts.googleapis.com/css2?family=Roboto:wght@400;500&family=Roboto+Condensed:wght@500;700&display=swap">
<style>
  :root {
    --page: #e8e5e1;
    --card-white: #f4f4f4;
    --brand-blue: #0b4391;
    --ink-blue: #0d4a97;
    --ink-grey: #5a5a5a;
    --band-grey: #6d6e70;
    --rule: #b9b9b9;
    --white: #ffffff;
  }
  * { margin: 0; padding: 0; box-sizing: border-box; }
  html, body { width: 1200px; height: 960px; overflow: hidden; }
  body {
    background: var(--page);
    position: relative;
    font-family: "Roboto", Arial, sans-serif;
  }
  .card {
    position: absolute;
    width: 600px;
    height: 343px;
    box-shadow: 0 2px 5px rgba(0,0,0,0.25);
    overflow: hidden;
  }
  .card--front { left: 314px; top: 113px; background: var(--card-white); }
  .card--back { left: 312px; top: 472px; background: var(--brand-blue); }

  .member-badge {
    position: absolute; left: 17px; top: 15px;
    width: 84px; height: 84px; border-radius: 50%;
    background: var(--white);
    border: 4px solid var(--brand-blue);
  }
  .brand {
    position: absolute; display: flex; align-items: center;
  }
  .brand__dot { border-radius: 50%; flex: none; }
  .brand__name { font-weight: 500; white-space: nowrap; }

  .card--front .brand { left: 64px; top: 134px; gap: 12px; }
  .card--front .brand__dot { width: 62px; height: 62px; border: 5px solid var(--band-grey); }
  .card--front .brand__name { font-size: 19px; color: var(--ink-blue); }

  .divider {
    position: absolute; left: 318px; top: 98px;
    width: 2px; height: 143px; background: var(--rule);
  }
  .contact { position: absolute; left: 345px; top: 97px; }
  .contact__name {
    font-family: "Roboto Condensed", Arial, sans-serif;
    font-weight: 700; font-size: 23px; color: var(--ink-blue);
    line-height: 1.1; text-transform: uppercase;
  }
  .contact__company {
    font-family: "Roboto Condensed", Arial, sans-serif;
    font-weight: 500; font-size: 16px; color: var(--ink-grey);
    text-transform: uppercase; letter-spacing: 0.3px; margin-top: 3px;
  }
  .contact__address { font-size: 14.5px; color: var(--ink-grey); line-height: 18px; margin-top: 11px; }
  .contact__line {
    display: flex; align-items: center; gap: 9px;
    font-size: 14.5px; color: var(--ink-grey); line-height: 20px;
  }
  .contact__line:first-of-type { margin-top: 7px; }
  .contact__icon { width: 13px; height: 13px; fill: var(--brand-blue); flex: none; }

  .web-band {
    position: absolute; left: 0; top: 303px; width: 600px; height: 25px;
    background: var(--brand-blue);
  }
  .web-band__grey {
    position: absolute; right: 0; top: 0; width: 118px; height: 25px; background: var(--band-grey);
  }
  .web-band__url {
    position: absolute; left: 136px; top: 4px;
    font-size: 14px; letter-spacing: 2.6px; color: var(--white);
  }
  .web-band__dot {
    position: absolute; left: 456px; top: -8px;
    width: 42px; height: 42px; border-radius: 50%;
    background: var(--white); border: 3px solid var(--brand-blue);
  }

  .card--back .brand { left: 132px; top: 122px; gap: 16px; }
  .card--back .brand__dot { width: 96px; height: 96px; border: 7px solid var(--white); }
  .card--back .brand__name { font-size: 32px; color: var(--white); }
  .services {
    position: absolute; left: 0; right: 0; top: 288px;
    text-align: center; color: var(--white); font-size: 15px;
  }
  .services__sep {
    display: inline-block; width: 7px; height: 7px; border-radius: 50%;
    background: var(--white); margin: 0 8px; vertical-align: middle;
  }
</style>
</head>
<body>
  <section class="card card--front">
    <div class="member-badge" role="img" aria-label="Continental Truthline Society member badge"></div>
    <div class="brand">
      <span class="brand__dot"></span>
      <span class="brand__name">Veritrace Kilonga</span>
    </div>
    <div class="divider"></div>
    <div class="contact">
      <p class="contact__name">Miriam Holloway</p>
      <p class="contact__company">Veritrace Kilonga</p>
      <p class="contact__address">PO Box 48317<br>Arusha, Tanzania</p>
      <p class="contact__line">
        <svg class="contact__icon" viewBox="0 0 24 24" aria-hidden="true"><path d="M6.6 10.8a15.1 15.1 0 0 0 6.6 6.6l2.2-2.2c.3-.3.7-.4 1-.2 1.1.4 2.3.6 3.6.6.6 0 1 .4 1 1V20c0 .6-.4 1-1 1A17 17 0 0 1 3 4c0-.6.4-1 1-1h3.5c.6 0 1 .4 1 1 0 1.3.2 2.5.6 3.6.1.3 0 .7-.2 1z"/></svg>
        +255 612 839 274
      </p>
      <p class="contact__line">
        <svg class="contact__icon" viewBox="0 0 24 24" aria-hidden="true"><path d="M2 5h20v14H2z M2 5l10 8 10-8" fill="none" stroke="#0b4391" stroke-width="2"/><path d="M3 6l9 7 9-7v12H3z"/></svg>
        miriamholloway@postvale.example
      </p>
    </div>
    <div class="web-band">
      <div class="web-band__grey"></div>
      <span class="web-band__url">www.miriamholloway.example</span>
    </div>
    <span class="web-band__dot" style="top:295px"></span>
  </section>

  <section class="card card--back">
    <div class="brand">
      <span class="brand__dot"></span>
      <span class="brand__name">Veritrace Kilonga</span>
    </div>
    <p class="services">Forensic Examinations<span class="services__sep"></span>Employment Screening</p>
  </section>
</body>
</html>
```